International oil and gas consultancy needs a business card design

We need a business card design for a new oil and gas consultancy business based in Perth Australia. This is a professional services business and needs a moderately conservative type of business card. The business card also needs to be simple and uncluttered. The colour of the business logo is dark red (see attached file).
The front of the card should have a white background and mainly black lettering and perhaps some use of dark red and/or grey (your choice).
The back of the card should have a light grey background with dark red, black and or both dark red & black lettering (your choice).
Please find attached a clear brief of how I would like the business card designed.
Updates

Hello Everyone, I have slightly modified the brief. The main change is to incorporate some dark red and grey colours into the card, while still keeping the black lettering dominant. I have made the changes in the attached detailed brief document. Regards

Please note, the front of the card must say Harbour Ledger Services (in addition to the logo).

Industry/Entity Type

Conservative

Requirements
Must have
• brief has been updated. please refer to attachment for details.

Front of the card MUST say Harbour Ledger Services (in addition to the logo)

```html
<!DOCTYPE html>
<html lang="en">
<head>
<meta charset="utf-8">
<title>Harbour Ledger Services – Business Card</title>
<link rel="stylesheet" href="https://fonts.googleapis.com/css2?family=Arimo:wght@400&family=Source+Sans+3:wght@400&display=swap">
<style>
  :root {
    --brand-red: #8e1c22;
    --ink: #111111;
    --muted-grey: #8a8a8a;
    --canvas-bg: #ffffff;
    --card-border: #6f6f6f;
    --back-bg: #f2f2f4;
    --row-bg: #ececec;
    --icon-bg: #ffffff;
  }
  html, body {
    margin: 0;
    padding: 0;
    width: 1200px;
    height: 1000px;
    overflow: hidden;
    background: var(--canvas-bg);
  }
  .canvas {
    position: relative;
    width: 1200px;
    height: 1000px;
  }
  .card {
    position: absolute;
    left: 277px;
    width: 667px;
    height: 393px;
    box-sizing: border-box;
    border: 1px solid var(--card-border);
    overflow: hidden;
  }

  /* Front */
  .card-front {
    top: 87px;
    background: linear-gradient(200deg, #ececec 0%, #ffffff 38%, #ffffff 100%);
    font-family: "Arimo", Arial, sans-serif;
    color: var(--ink);
  }
  .front-brand {
    position: absolute;
    left: 18px;
    top: 113px;
    display: flex;
    align-items: center;
    gap: 10px;
    font-size: 27px;
    white-space: nowrap;
    color: var(--brand-red);
  }
  .brand-mark {
    flex: 0 0 auto;
    width: 18px;
    height: 18px;
    background: var(--brand-red);
  }
  .holder {
    position: absolute;
    right: 12px;
    text-align: right;
    margin: 0;
    font-weight: 400;
    white-space: nowrap;
  }
  .holder-name { top: 14px; font-size: 26px; }
  .holder-title { top: 69px; font-size: 20px; }
  .holder-company { top: 120px; font-size: 20px; }

  .contact-list {
    position: absolute;
    left: 280px;
    top: 217px;
    margin: 0;
    padding: 0;
    list-style: none;
  }
  .contact-row {
    display: flex;
    align-items: center;
    gap: 4px;
    height: 30px;
    margin-bottom: 15.5px;
  }
  .contact-icon {
    width: 28px;
    height: 28px;
    box-sizing: border-box;
    border: 1px solid #e2e2e2;
    background: var(--icon-bg);
    display: flex;
    align-items: center;
    justify-content: center;
  }
  .contact-icon svg { width: 13px; height: 13px; }
  .contact-text {
    width: 351px;
    height: 30px;
    box-sizing: border-box;
    background: linear-gradient(90deg, #ffffff 0%, #ffffff 55%, var(--row-bg) 100%);
    border: 1px solid #eeeeee;
    font-size: 18px;
    line-height: 28px;
    text-align: center;
    white-space: nowrap;
  }
  .abn {
    position: absolute;
    left: 13px;
    bottom: 9px;
    margin: 0;
    font-size: 11px;
  }

  /* Back */
  .card-back {
    top: 525px;
    background: var(--back-bg);
    font-family: "Source Sans 3", "Myriad Pro", sans-serif;
    color: var(--ink);
  }
  .back-brand {
    position: absolute;
    left: 0;
    top: 150px;
    width: 360px;
    display: flex;
    align-items: center;
    justify-content: center;
    gap: 10px;
    font-size: 26px;
    line-height: 32px;
    white-space: nowrap;
    color: var(--brand-red);
  }
  .tagline {
    position: absolute;
    left: 0;
    top: 220px;
    width: 360px;
    margin: 0;
    text-align: center;
    font-size: 18px;
    line-height: 24px;
  }
  .divider {
    position: absolute;
    left: 356px;
    top: 55px;
    width: 2px;
    height: 262px;
    background: linear-gradient(180deg, rgba(170,170,170,0) 0%, #a9a9a9 50%, rgba(170,170,170,0) 100%);
  }
  .services {
    position: absolute;
    left: 411px;
    top: 104px;
  }
  .services-heading {
    margin: 0 0 21px 0;
    font-size: 22px;
    line-height: 28px;
    font-weight: 400;
  }
  .services-list {
    margin: 0;
    padding: 0;
    list-style: none;
  }
  .services-list li {
    position: relative;
    padding-left: 15px;
    font-size: 18px;
    line-height: 24px;
    margin-bottom: 24px;
  }
  .services-list li::before {
    content: "";
    position: absolute;
    left: -5px;
    top: 9px;
    width: 8px;
    height: 8px;
    border-radius: 50%;
    background: var(--brand-red);
  }
</style>
</head>
<body>
<main class="canvas">

  <section class="card card-front" aria-label="Business card front">
    <div class="front-brand"><span class="brand-mark"></span>Harbour Ledger Services</div>

    <h1 class="holder holder-name">Neil Ashford</h1>
    <p class="holder holder-title">Director</p>
    <p class="holder holder-company">Harbour Ledger Services</p>

    <ul class="contact-list">
      <li class="contact-row">
        <span class="contact-icon">
          <svg viewBox="0 0 16 16"><path d="M8 1.5a4.5 4.5 0 0 0-4.5 4.5c0 3.4 4.5 8.5 4.5 8.5s4.5-5.1 4.5-8.5A4.5 4.5 0 0 0 8 1.5z" fill="none" stroke="#8e1c22" stroke-width="1.6"/><circle cx="8" cy="6" r="1.6" fill="#8e1c22"/></svg>
        </span>
        <span class="contact-text">Region: Australasia and South East Asia</span>
      </li>
      <li class="contact-row">
        <span class="contact-icon">
          <svg viewBox="0 0 16 16"><circle cx="8" cy="8" r="6.8" fill="none" stroke="#8e1c22" stroke-width="1.4"/><path d="M5.4 4.6l1.3-.3.8 1.9-.9.7c.5 1 1.2 1.8 2.2 2.3l.7-.9 1.9.8-.3 1.3c-2.7.2-5.9-3-5.7-5.8z" fill="#8e1c22"/></svg>
        </span>
        <span class="contact-text">Phone: +61&nbsp; (0)400 318 529</span>
      </li>
      <li class="contact-row">
        <span class="contact-icon">
          <svg viewBox="0 0 16 16"><rect x="1.5" y="3.5" width="13" height="9" fill="none" stroke="#8e1c22" stroke-width="1.5"/><path d="M1.5 3.5L8 9l6.5-5.5" fill="none" stroke="#8e1c22" stroke-width="1.5"/></svg>
        </span>
        <span class="contact-text">Email: neil@harbourledger.com</span>
      </li>
      <li class="contact-row">
        <span class="contact-icon">
          <svg viewBox="0 0 16 16"><circle cx="8" cy="8" r="6.5" fill="none" stroke="#8e1c22" stroke-width="1.5"/><path d="M1.5 8h13M8 1.5c-2.4 2.2-2.4 10.8 0 13M8 1.5c2.4 2.2 2.4 10.8 0 13" fill="none" stroke="#8e1c22" stroke-width="1.2"/></svg>
        </span>
        <span class="contact-text">Website: www.harbourledger.com</span>
      </li>
    </ul>

    <p class="abn">ABN: 52 104 876 203</p>
  </section>

  <section class="card card-back" aria-label="Business card back">
    <div class="back-brand"><span class="brand-mark"></span>Harbour Ledger Services</div>
    <p class="tagline">Special Finaanacial Consultants<br>to the Oil and Gas Industry</p>

    <div class="divider"></div>

    <div class="services">
      <h2 class="services-heading">Services Provided:</h2>
      <ul class="services-list">
        <li>Joint Venture Audits</li>
        <li>Contract Audits</li>
        <li>Operational Audits</li>
      </ul>
    </div>
  </section>

</main>
</body>
</html>
```